verdant terraces simple classy business card design

my name is colin barrow and I run a gardening business aimed at high class verdant terraces. the business name is verdant terraces and our logo was designed on pixel harbour .My clientel are anything from residential homes to businesses. I take pride in my work and know that I offer a service like no other in my area.
The business card will be used to represent my business and I want it to be not only rememberable, but simplistic and modern. Eye catching too. Of course I would like it relatable to gardening and appealing to the correct clientel - those being garden enthusiasts, prestigious homes and businesses that are after top of the line gardening services like no other on the market.
I am not a typical lawn mowing business so I don't want a typical card design that represents that. The gardens I work with are generally million dollar properties with owners who are very garden proud looking for upkeep and guidance from me along with sometimes whole new garden designs. I want the business cards to show to my clients that I take pride, as they do, in their garden. And I want them to know from my card that I am a professional, qualified horticulturist offering them a top of the line service for life. I want them to refer my business on. I want them to look at my business card and see class and professionalism in a modern unique bold way.
The card should be simple with the possibility of the logo on the front being embossed/debossed and my details on the back the card should have a organic garden feel it's very important to me that it is absolutely perfect
I am also very open to ideas and suggestions so look forward to seeing the designs. the business logo has been supplied with this project and I want the card to be double sided

Contact info is
Colin Barrow - Managing Director / Horticulturist
Phone : 0481 526 704
Email: colinbarrow@verdantterraces.example.au

Target Market(s)

high class gardens residential and commercial

Industry/Entity Type

Gardener

Contact Information for Business Card

Contact info is
Phone : 0481 526 704

PLEASE MAKE CARD DOUBLE SIDED

Requirements
Must have
• organic simple classy modern feel
• must flow with the current logo that has been supplied with this project
• Double sided
• Must explain in a simple way that I deal with high end gardens and I'm a qualified horticulturist
Nice to have
• embossed debossed logo
Should not have
• shouldn't be to busy or cheap looking

```html
<!DOCTYPE html>
<html lang="en">
<head>
<meta charset="utf-8">
<title>Verdant Terraces – Business Card</title>
<link href="https://fonts.googleapis.com/css2?family=Didact+Gothic&family=Questrial&display=swap" rel="stylesheet">
<style>
  :root {
    --backdrop: #e9e6e1;
    --card: #f1efeb;
    --card-edge: #dcd8d1;
    --ink: #2b2b2b;
    --ink-soft: #4a4a4a;
    --rule: #3a3a3a;
    --leaf: #4a9a48;
  }
  * { box-sizing: border-box; margin: 0; padding: 0; }
  html, body {
    width: 1200px;
    height: 918px;
    overflow: hidden;
    background: var(--backdrop);
  }
  .sheet {
    width: 1200px;
    height: 918px;
    display: flex;
    flex-direction: column;
    align-items: center;
    justify-content: center;
    gap: 48px;
  }
  .card {
    position: relative;
    width: 640px;
    height: 384px;
    background: var(--card);
    border: 1px solid var(--card-edge);
    box-shadow: 0 2px 10px rgba(0,0,0,0.08);
    overflow: hidden;
  }

  /* Back: contact details */
  .details {
    position: absolute;
    left: 56px;
    top: 56px;
    width: 320px;
    font-family: "Questrial", "Didact Gothic", sans-serif;
    color: var(--ink);
  }
  .details__name {
    font-family: "Didact Gothic", sans-serif;
    font-size: 20px;
    letter-spacing: 0.2px;
    -webkit-text-stroke: 0.5px var(--ink);
  }
  .details__title {
    font-size: 14px;
    color: var(--ink-soft);
    margin-top: 4px;
  }
  .details__rule {
    border: none;
    border-top: 1.5px solid var(--rule);
    margin: 12px 0 14px;
  }
  .details__row {
    display: flex;
    align-items: center;
    gap: 12px;
    font-size: 14px;
    color: var(--ink-soft);
    margin-bottom: 9px;
  }
  .details__icon { width: 14px; height: 14px; flex: none; }
  .details__rule--end { margin-top: 8px; }

  /* Front: brand name */
  .brand {
    position: absolute;
    left: 0;
    right: 0;
    top: 150px;
    display: flex;
    align-items: center;
    justify-content: center;
    gap: 24px;
  }
  .brand__dot {
    width: 64px;
    height: 64px;
    border-radius: 50%;
    background: var(--leaf);
  }
  .brand__name {
    font-family: "Didact Gothic", sans-serif;
    font-weight: 400;
    color: var(--leaf);
    text-transform: uppercase;
    line-height: 1.05;
  }
  .brand__line1 { display: block; font-size: 50px; letter-spacing: 4px; }
  .brand__line2 { display: block; font-size: 26px; letter-spacing: 19px; margin-top: 4px; }
</style>
</head>
<body>
  <main class="sheet">
    <section class="card card--back" aria-label="Card back">
      <div class="details">
        <p class="details__name">Colin Barrow</p>
        <p class="details__title">Managing Director / Horticulturist</p>
        <hr class="details__rule">
        <p class="details__row">
          <svg class="details__icon" viewBox="0 0 24 24" aria-hidden="true"><path fill="#333" d="M6.6 10.8a15.2 15.2 0 0 0 6.6 6.6l2.2-2.2c.3-.3.7-.4 1-.2 1.1.4 2.3.6 3.6.6.6 0 1 .4 1 1V20c0 .6-.4 1-1 1A17 17 0 0 1 3 4c0-.6.4-1 1-1h3.5c.6 0 1 .4 1 1 0 1.3.2 2.5.6 3.6.1.3 0 .7-.2 1z"/></svg>
          0481 526 704
        </p>
        <p class="details__row">
          <svg class="details__icon" viewBox="0 0 24 24" aria-hidden="true"><rect x="2" y="5" width="20" height="14" fill="none" stroke="#333" stroke-width="2"/><path d="M2 6l10 7 10-7" fill="none" stroke="#333" stroke-width="2"/></svg>
          colinbarrow@verdantterraces.example.au
        </p>
        <hr class="details__rule details__rule--end">
      </div>
    </section>

    <section class="card card--front" aria-label="Card front">
      <div class="brand">
        <span class="brand__dot" aria-hidden="true"></span>
        <h1 class="brand__name">
          <span class="brand__line1">Verdant</span>
          <span class="brand__line2">Terraces</span>
        </h1>
      </div>
    </section>
  </main>
</body>
</html>
```